LANTERN - and the quiet crafts of everyday life

I´m writing a book about CHANGE and the skills leaders needs to embody the transformation from being amanager to become leaders.
The title of the book in Icelandic is the same as the name of the project (which I want to be used on the designes is:) UPPSPRETTA
(with the subtitle:) og hugrekki hversdagsins

Change is not controlled or managed – Leading effective change is an art form which is one of the big reasons for why 70% of changes within companies fail. The main reason however, is that managers are tasked with managing and directing them. The art form of change is to put it in the hands of leaders who possess the emotional intelligence that is needed – all their other advantages intact – to lead change all the way.

The big problem when it comes to change is that there are too many managers and too few leaders within companies – leaders who possess emotional intelligence which is the most important skill a leader embodies to empower change. A leader has what it takes to empower followership.

A manager tends to push and control, make decisions that he presupposes others to implement the way he expects. An emotionally competent leader leads by example and enhances followership on that journey because of the trust and respect he has earned.

In few words: SOFT SKILLS ARE THE NEW HARD SKILLS!

```html
<!DOCTYPE html>
<html lang="is">
<head>
<meta charset="utf-8">
<title>UPPSPRETTA – og hugrekki hversdagsins</title>
<link rel="stylesheet" href="https://fonts.googleapis.com/css2?family=Tinos&family=Crimson+Pro:wght@600&display=swap">
<style>
  :root {
    --stage: #1e1e1e;
    --cover-orange: #f59a38;
    --cover-orange-low: #e99337;
    --ink-white: #ffffff;
    --ink-brown: #7b3f16;
    --ink-body: #ffffff;
  }
  html, body {
    margin: 0;
    padding: 0;
    width: 1200px;
    height: 1200px;
    overflow: hidden;
    background: var(--stage);
  }
  .cover-wrap {
    position: absolute;
    left: 30px;
    top: 201px;
    width: 1140px;
    height: 798px;
    background: var(--cover-orange);
    font-family: "Tinos", "Times New Roman", serif;
    color: var(--ink-white);
    overflow: hidden;
  }
  .front-lower {
    position: absolute;
    left: 608px;
    top: 393px;
    width: 532px;
    height: 405px;
    background: var(--cover-orange-low);
  }
  /* back cover */
  .back-cover {
    position: absolute;
    left: 45px;
    top: 0;
    width: 443px;
  }
  .back-title {
    position: absolute;
    top: 66px;
    left: -40px;
    right: -40px;
    margin: 0;
    text-align: center;
    font-weight: 400;
    font-size: 40px;
    line-height: 1;
    letter-spacing: 0.13em;
  }
  .back-subtitle {
    position: absolute;
    top: 108px;
    left: -40px;
    right: -40px;
    margin: 0;
    text-align: center;
    font-family: "Crimson Pro", "Times New Roman", serif;
    font-weight: 600;
    font-size: 23px;
    line-height: 1.1;
    color: var(--ink-brown);
  }
  .back-blurb {
    position: absolute;
    top: 154px;
    left: 0;
    width: 443px;
  }
  .back-blurb p {
    margin: 0 0 22px;
    font-size: 16.6px;
    line-height: 22.1px;
    text-align: justify;
    text-align-last: center;
    color: var(--ink-body);
  }
  /* spine */
  .spine-text {
    position: absolute;
    left: 550px;
    width: 38px;
    margin: 0;
    writing-mode: vertical-rl;
    font-weight: 400;
    font-size: 37px;
    line-height: 38px;
    letter-spacing: 0.14em;
    white-space: nowrap;
  }
  .spine-title { top: 66px; }
  .spine-author { top: 481px; font-size: 31px; letter-spacing: 0.12em; }
  /* front cover */
  .front-cover {
    position: absolute;
    left: 608px;
    top: 0;
    width: 532px;
    height: 798px;
    text-align: center;
  }
  .front-title {
    position: absolute;
    top: 58px;
    left: 0;
    right: 0;
    margin: 0;
    font-weight: 400;
    font-size: 57px;
    line-height: 1;
    letter-spacing: 0.14em;
    padding-left: 0.14em;
  }
  .front-subtitle {
    position: absolute;
    top: 132px;
    left: 0;
    right: 0;
    margin: 0;
    font-family: "Crimson Pro", "Times New Roman", serif;
    font-weight: 600;
    font-size: 26px;
    line-height: 1.1;
    color: var(--ink-brown);
  }
  .front-author {
    position: absolute;
    top: 704px;
    left: 0;
    right: 0;
    margin: 0;
    font-size: 44px;
    line-height: 1;
    letter-spacing: 0.12em;
    padding-left: 0.12em;
  }
  .hero-figure {
    position: absolute;
    left: 218px;
    top: 199px;
  }
</style>
</head>
<body>
  <main class="cover-wrap">
    <div class="front-lower"></div>

    <section class="back-cover">
      <h2 class="back-title">UPPSPRETTA</h2>
      <p class="back-subtitle">og hugrekki hversdagsins</p>
      <div class="back-blurb">
        <p>Lorem ipsum dolor sit amet, consectetur adipiscing elit, sed do eiusmod tempor incididunt ut labore et dolore magna aliqua. Quis ipsum suspendisse ultrices gravida. Risus commodo viverra maecenas accumsan lacus vel facilisis. Lorem ipsum dolor sit amet, consectetur adipiscing elit, sed do eiusmod tempor incididunt ut labore et dolore magna aliqua. Quis ipsum suspendisse ultrices gravida. Risus commodo viverra maecenas accumsan lacus vel facilisis.</p>
        <p>Lorem ipsum dolor sit amet, consectetur adipiscing elit, sed do eiusmod tempor incididunt ut labore et dolore magna aliqua. Quis ipsum suspendisse ultrices gravida. Risus commodo viverra maecenas accumsan lacus vel facilisis. Lorem ipsum dolor sit amet, consectetur adipiscing elit, sed do eiusmod tempor incididunt ut labore et dolore magna aliqua. Quis ipsum suspendisse ultrices gravida. Risus commodo viverra maecenas accumsan lacus vel facilisis. Lorem ipsum dolor sit amet, consectetur adipiscing elit, sed do eiusmod tempor incididunt ut labore et dolore magna aliqua. Quis ipsum suspendisse ultrices gravida. Risus commodo viverra maecenas accumsan lacus vel facilisis. s gravida. Risus commodo viverra maecenas accumsan lacus vel facilisis. s gravida. Risus commodo viverra maecenas accumsan lacus vel facilisis.</p>
      </div>
    </section>

    <p class="spine-text spine-title">UPPSPRETTA</p>
    <p class="spine-text spine-author">AUTHOR NAME</p>

    <section class="front-cover">
      <h1 class="front-title">UPPSPRETTA</h1>
      <p class="front-subtitle">og hugrekki hversdagsins</p>
      <svg class="hero-figure" width="96" height="476" viewBox="0 0 96 476" role="img" aria-label="Photograph of a black chess pawn standing on a surface, its reflection below shaped as a bronze king">
        <defs>
          <linearGradient id="figure-tone" x1="0" y1="0" x2="0" y2="1">
            <stop offset="0" stop-color="#1c1c1c"/>
            <stop offset="0.41" stop-color="#262626"/>
            <stop offset="0.41" stop-color="#b87430"/>
            <stop offset="1" stop-color="#c98a45"/>
          </linearGradient>
        </defs>
        <rect x="0" y="0" width="96" height="476" rx="40" fill="url(#figure-tone)"/>
      </svg>
      <p class="front-author">AUTHOR NAME</p>
    </section>
  </main>
</body>
</html>
```